Structural Engineering Business Card

Brookvane Drafting does residential house plans for clients in Central Florida. Would like simple but elegant business card that is appropriate for a house plan engineering company. Prefer black business card with black/white them but open to other shades of blue. I uploaded a sample card that I came across that looked good but please come up with your own creative designs.

Contact Information for Business Card

Name, Title, Phone, Email, Address, website

```html
<!DOCTYPE html>
<html lang="en">
<head>
<meta charset="utf-8">
<title>Brookvane Drafting – Business Card</title>
<link rel="stylesheet" href="https://fonts.googleapis.com/css2?family=Poppins:wght@400;500;700&display=swap">
<style>
  :root {
    --stage: #c9c9c9;
    --ink: #000000;
    --paper: #ffffff;
    --rule: #8a8a8a;
  }
  * { margin: 0; padding: 0; box-sizing: border-box; }
  html, body { width: 1200px; height: 1200px; overflow: hidden; }
  body {
    background: var(--stage);
    font-family: "Poppins", sans-serif;
    position: relative;
  }
  .card {
    position: absolute;
    top: 303px;
    width: 368px;
    height: 594px;
    overflow: hidden;
    box-shadow: 3px 4px 6px rgba(0,0,0,0.35);
  }
  .card--back { left: 200px; background: var(--ink); }
  .card--front { left: 599px; background: var(--ink); }

  .wordmark {
    position: absolute;
    left: 0; right: 0;
    text-align: center;
    font-weight: 700;
    font-size: 23px;
    letter-spacing: 0.5px;
    text-transform: uppercase;
    line-height: 1;
  }
  .card--back .wordmark { top: 492px; color: var(--paper); }

  .front-top {
    position: absolute;
    left: 0; top: 0;
    width: 100%;
    height: 284px;
    background: var(--paper);
  }
  .front-top .wordmark { top: 138px; color: var(--ink); }
  .split-line {
    position: absolute;
    left: 0; top: 289px;
    width: 100%;
    height: 3px;
    background: var(--paper);
  }

  .details {
    position: absolute;
    left: 0; right: 0;
    top: 336px;
    text-align: center;
    color: var(--paper);
  }
  .person-name { font-weight: 700; font-size: 20px; line-height: 24px; letter-spacing: 0.3px; }
  .person-title { font-weight: 400; font-size: 16px; line-height: 22px; }

  .icon-row {
    display: flex;
    align-items: center;
    justify-content: center;
    gap: 5px;
    margin-top: 14px;
  }
  .icon-row .rule { width: 52px; height: 1px; background: var(--rule); margin: 0 3px; }
  .icon-box {
    width: 25px; height: 25px;
    background: var(--paper);
    border-radius: 3px;
    display: flex; align-items: center; justify-content: center;
  }
  .icon-box svg { width: 16px; height: 16px; }

  .contact-lines { margin-top: 6px; font-size: 16px; line-height: 21px; }
  .divider { width: 195px; height: 1px; background: var(--rule); margin: 14px auto 12px; }
  .address { font-size: 16px; line-height: 21px; }
</style>
</head>
<body>
  <section class="card card--back" role="img" aria-label="Black card back with the Brookvane Drafting name">
    <div class="wordmark">Brookvane Drafting</div>
  </section>

  <section class="card card--front">
    <div class="front-top">
      <div class="wordmark">Brookvane Drafting</div>
    </div>
    <div class="split-line"></div>

    <div class="details">
      <div class="person-name">MARCUS ELLERY</div>
      <div class="person-title">Managing Director</div>

      <div class="icon-row">
        <span class="rule"></span>
        <span class="icon-box" aria-label="Phone">
          <svg viewBox="0 0 16 16"><path d="M2 6c0-2 3-3 6-3s6 1 6 3v1h-3V5.5H5V7H2z M4 8h8l1 5H3z" fill="#000"/><circle cx="8" cy="10.5" r="1.4" fill="#fff"/></svg>
        </span>
        <span class="icon-box" aria-label="Email">
          <svg viewBox="0 0 16 16"><rect x="1.5" y="3.5" width="13" height="9" fill="none" stroke="#000" stroke-width="1.3"/><path d="M1.5 3.5 8 9l6.5-5.5M1.5 12.5l5-4.5M14.5 12.5l-5-4.5" fill="none" stroke="#000" stroke-width="1.1"/></svg>
        </span>
        <span class="icon-box" aria-label="Website">
          <svg viewBox="0 0 16 16"><circle cx="8" cy="8" r="6.5" fill="#000"/><path d="M5 4.5c1.5 0 2 1 1.5 2S4.5 8 5.5 9.5 7 12 6.5 13.5M10 3.5c-.5 1.5.5 2.5 2 2.5M11 9c-1 0-1.5 1-1 2" fill="none" stroke="#fff" stroke-width="1.1"/></svg>
        </span>
        <span class="rule"></span>
      </div>

      <div class="contact-lines">
        <div>407-555 018 362</div>
        <div>hello@brookvanedrafting.com</div>
        <div>www.brookvanedrafting.com</div>
      </div>

      <div class="divider"></div>

      <div class="address">
        <div>218, Larkspur Lane, Suite 4</div>
        <div>32801, Orlando, FL</div>
      </div>
    </div>
  </section>
</body>
</html>
```